WP website design (Harrowgate)

We need a wordpress design for an established auction and real estate company based in Florida. The winning design will incorporate a professional color scheme with company logo in a clean layout. The design needs to consider that this will be developed on a responsive theme. Colors are those that will highlight the logo.

Industry/Entity Type

Real Estate

Font styles to use
Serif
Sans Serif

Colors

Designer to choose colors to be used in the design.

Requirements
Must have
• Navigation:
1) Home
2) Auctions
3) Online Auctions
4) About Us
5) Services
6) Real Estate Listings
7) References
8) Contact Us

Colors will be blue (#000066) / red (#B10000) and black or other complementary color. Tagline to be used "Since 1977, Proven Results." Slideshow to be placed in the header or body of home page - please use stock real estate image.

Widgets: 1) Email Sign-up 2) Social media icons for FB and LinkedIn 3) Featured Listings 4) Testimonials 5) Register button

Footer will have smaller company logo, attached logos and contact info:
Phone: (555) 261-0948 Mobile: (555) 718-3062
Email: mirelharrowgate@quellmail.example
Address: 58 E. Tamsin Avenue, Ste 410, Corvel Bay, FL 32599
Nice to have
• Use of a drop down menu:
Auctions-
1) Upcoming Auctions
2) Past Auctions

```html
<!DOCTYPE html>
<html lang="en">
<head>
<meta charset="utf-8">
<title>Harrowgate Auctions</title>
<link href="https://fonts.googleapis.com/css2?family=Arimo:wght@400;700&family=Raleway:wght@400;500&family=Rubik:wght@500;700&display=swap" rel="stylesheet">
<style>
:root{
  --navy:#1f1a8f;
  --nav:#1c1b8c;
  --panel-head:#2b2b86;
  --red:#d8212c;
  --text:#333333;
  --footer:#3b3b3b;
  --border:#d6d6d6;
}
*{margin:0;padding:0;box-sizing:border-box}
html,body{width:918px;height:1200px;overflow:hidden;background:#fff}
body{position:relative;font-family:Arimo,Arial,sans-serif;color:var(--text)}
.abs{position:absolute}

.brand{left:77px;top:16px;display:flex;align-items:center;gap:10px}
.brand-mark{width:56px;height:58px;background:var(--navy)}
.brand-name{font-family:Rubik,sans-serif;font-weight:700;font-size:29px;color:var(--navy);letter-spacing:-.5px}

.contact-top{right:77px;top:23px;display:flex;align-items:center;gap:8px;font-weight:700;font-size:13.5px;color:#111}
.social{width:27px;height:27px;border-radius:50%}
.social.one{background:#1a78bf}
.social.two{background:#2d4f9b}
.divider-v{width:1px;height:26px;background:#222;margin:0 2px}
.email-top{right:77px;top:61px;display:flex;align-items:center;gap:9px;font-size:14.5px;color:var(--red)}

.main-nav{left:0;top:91px;width:918px;height:40px;background:var(--nav)}
.main-nav ul{list-style:none;display:flex;justify-content:space-between;margin:0 77px;height:40px;align-items:center}
.main-nav li{color:#fff;font-size:11.2px;height:24px;line-height:24px;border-right:1px solid #4a48b0;flex:auto;text-align:center}
.main-nav li:first-child{text-align:left;flex:0 0 46px}
.main-nav li:last-child{border:none;text-align:right}

.hero{left:77px;top:141px;width:764px;height:301px;border:4px solid #000;background:linear-gradient(180deg,#8cc06b 0%,#c9d3c6 40%,#e7e1d8 62%,#6f8f4a 100%)}
.slide-arrow{top:243px}

.welcome{left:77px;top:458px}
.welcome-title{display:flex;align-items:center;gap:10px;font-family:Rubik,sans-serif;font-weight:700;font-size:17px;color:var(--navy)}
.welcome-title .mark{width:22px;height:22px;background:var(--navy)}
.welcome-title .accent{color:var(--red)}
.welcome-rule{width:206px;height:2px;margin-top:6px;background:linear-gradient(90deg,#999 0 100px,#ccc 100px)}
.intro{left:77px;top:495px;width:765px;font-family:Raleway,sans-serif;font-size:9.8px;line-height:18.4px;color:#444;text-align:justify}

.listings{left:77px;width:485px}
.listings-head{height:30px;background:var(--panel-head);color:#fff;font-family:Raleway,sans-serif;font-weight:500;font-size:12.4px;line-height:30px;padding-left:11px}
.listings-body{border:1px solid var(--border);border-top:none;background:linear-gradient(180deg,#fff,#efefef);padding:14px 10px 0 10px}
.listing{display:flex;gap:34px;height:84px}
.listing-photo{width:96px;height:71px;border:2px solid #1d62b3;background:linear-gradient(135deg,#2e79c8,#9fc3e6 55%,#d9c9a6);flex:none}
.listing-text{width:300px}
.listing h3{font-weight:400;font-size:10.6px;color:var(--red);margin:3px 0 3px}
.listing p{font-size:9.6px;line-height:13.8px;color:#222}

.register{left:613px;top:617px;width:228px;height:42px;border-radius:4px;background:linear-gradient(180deg,#e94148,#d41e27 55%,#c51720);color:#fff;font-family:Rubik,sans-serif;font-weight:700;font-size:19px;text-align:center;line-height:42px;letter-spacing:.5px}

.widget{left:613px;width:228px;border:1px solid var(--border);border-radius:6px;background:linear-gradient(180deg,#fff,#efefef)}
.signup{top:675px;height:152px;padding:18px 14px}
.signup h2{font-family:Raleway,sans-serif;font-weight:500;font-size:17px;color:#2222b8;letter-spacing:.5px;margin-bottom:8px}
.field{width:192px;height:19px;border:1px solid #bbb;background:#fff;font-size:9px;color:#999;padding-left:5px;line-height:17px;margin-bottom:12px}
.submit{width:77px;height:23px;background:var(--red);color:#fff;font-size:12px;line-height:23px;text-align:center;border-radius:2px}

.testimonials{top:855px;height:169px;padding:10px 30px 10px 22px}
.testimonials h2{font-family:Rubik,sans-serif;font-weight:700;font-size:15px;color:var(--red);margin-left:-2px;letter-spacing:.5px;margin-bottom:6px}
.quote{font-family:Arimo,sans-serif;font-size:9.8px;line-height:16.8px;color:#333;text-align:justify;position:relative}
.quote .open{position:absolute;left:-14px;top:-4px;font-size:18px;color:#555;font-family:Georgia,serif}
.quote .close{position:absolute;right:0;bottom:-20px;font-size:18px;color:var(--red);font-family:Georgia,serif}

.site-footer{left:0;top:1107px;width:918px;height:93px;background:var(--footer);color:#fff}
.footer-contact{text-align:center;font-size:9.6px;margin-top:17px;word-spacing:1px}
.footer-contact span{margin:0 7px}
.footer-badges{display:flex;align-items:center;justify-content:center;gap:16px;margin-top:13px}
.footer-brand{display:flex;align-items:center;gap:7px;font-family:Rubik,sans-serif;font-weight:700;font-size:17px;color:#eee}
.footer-brand .mark{width:30px;height:30px;background:#ddd}
.badge{background:#cfcfcf}
</style>
</head>
<body>

<header>
  <div class="abs brand"><div class="brand-mark"></div><span class="brand-name">Harrowgate</span></div>
  <div class="abs contact-top">
    <span class="social one"></span><span class="social two"></span>
    <span class="divider-v"></span>
    <svg width="24" height="24" viewBox="0 0 24 24"><circle cx="12" cy="12" r="11" fill="none" stroke="#d8212c" stroke-width="1.6"/><path d="M8 6c-1 1-1 3 1 6s4 5 6 5c1 0 2-1 2-2l-2-2-2 1c-1-1-2-2-3-4l1-2-2-2z" fill="#d8212c"/></svg>
    <span>(555) 261-0948</span>
  </div>
  <div class="abs email-top">
    <svg width="30" height="20" viewBox="0 0 30 20"><rect width="30" height="20" fill="#111"/><path d="M1 1l14 11L29 1" stroke="#fff" stroke-width="1.6" fill="none"/><path d="M1 19l10-9M29 19L19 10" stroke="#fff" stroke-width="1.2"/></svg>
    <span>Email: mirelharrowgate@quellmail.example</span>
  </div>
</header>

<nav class="abs main-nav">
  <ul>
    <li>HOME</li><li>AUCTIONS</li><li>ONLINE AUCTIONS</li><li>ABOUT US</li><li>SERVICES</li><li>REAL ESTATE LISTINGS</li><li>REFERENCES</li><li>CONTACT US</li>
  </ul>
</nav>

<div class="abs hero" role="img" aria-label="Slideshow photo: real estate agent in a suit standing before a suburban house with trees and shrubs"></div>
<svg class="abs slide-arrow" style="left:44px" width="22" height="44" viewBox="0 0 22 44"><path d="M19 2L3 22l16 20" stroke="#444" stroke-width="2.5" fill="none"/></svg>
<svg class="abs slide-arrow" style="left:852px" width="22" height="44" viewBox="0 0 22 44"><path d="M3 2l16 20L3 42" stroke="#444" stroke-width="2.5" fill="none"/></svg>

<section class="abs welcome">
  <div class="welcome-title"><span class="mark"></span><span>Welcome <span class="accent">Harrowgate</span></span></div>
  <div class="welcome-rule"></div>
</section>
<p class="abs intro">Lorem Ipsum has been the industry's standard dummy text ever since the 1500s, when an unknown printer took a galley of type and scrambled it to make a type specimen book. It has survived not only five centuries, but also the leap into electronic typesetting, remaining essentially unchanged. It was popularised in the 1960s with the release of Vellumark sheets containing Lorem Ipsum passages, and more recently with desktop publishing software like Quire Layout including versions of Lorem Ipsum.Lorem Ipsum passages, and more recently with desktop publishing software like Quire Layout including versions of Lorem Ipsum.</p>

<section class="abs listings" style="top:615px">
  <div class="listings-head">FAMILY OWNED AND OPERATED WITH A FAMILY GUARANTEE</div>
  <div class="listings-body" style="height:182px">
    <article class="listing"><div class="listing-photo" role="img" aria-label="Hand holding house keys in front of a building"></div><div class="listing-text"><h3>FURNITURE ‘ ANTIQUES ‘ COLLECTIBLES</h3><p>Lorem Ipsum is that it has a more-or-less normal distribution of letters, as opposed to using 'Content here, content here', making it look like readable English. Many desktop publishing packages</p></div></article>
    <article class="listing"><div class="listing-photo" role="img" aria-label="Hand holding house keys in front of a building"></div><div class="listing-text"><h3>FURNITURE ‘ ANTIQUES ‘ COLLECTIBLES</h3><p>Lorem Ipsum is that it has a more-or-less normal distribution of letters, as opposed to using 'Content here, content here', making it look like readable English. Many desktop publishing packages</p></div></article>
  </div>
</section>

<section class="abs listings" style="top:853px">
  <div class="listings-head">FAMILY OWNED AND OPERATED WITH A FAMILY GUARANTEE</div>
  <div class="listings-body" style="height:183px">
    <article class="listing"><div class="listing-photo" role="img" aria-label="Hand holding house keys in front of a building"></div><div class="listing-text"><h3>FURNITURE ‘ ANTIQUES ‘ COLLECTIBLES</h3><p>Lorem Ipsum is that it has a more-or-less normal distribution of letters, as opposed to using 'Content here, content here', making it look like readable English. Many desktop publishing packages</p></div></article>
    <article class="listing"><div class="listing-photo" role="img" aria-label="Hand holding house keys in front of a building"></div><div class="listing-text"><h3>FURNITURE ‘ ANTIQUES ‘ COLLECTIBLES</h3><p>Lorem Ipsum is that it has a more-or-less normal distribution of letters, as opposed to using 'Content here, content here', making it look like readable English. Many desktop publishing packages</p></div></article>
  </div>
</section>

<div class="abs register">REGISTER NOW</div>

<aside class="abs widget signup">
  <h2>EMAIL SIGN UP</h2>
  <div class="field">Your Name</div>
  <div class="field">Your Email Address</div>
  <div class="submit">SUBMET</div>
</aside>

<aside class="abs widget testimonials">
  <h2>Testimonials Blog</h2>
  <p class="quote"><span class="open">“</span>simply dummy text of the printing and typesetting industry. Lorem Ipsum has been the industry's standard dummy text ever since the 1500s, when an unknown dummy text ever since print-er took a galley of type and scrambled it to make a type.<span class="close">”</span></p>
</aside>

<footer class="abs site-footer">
  <div class="footer-contact"><span>Phone: (555) 261-0948</span>|<span>Mobile: (555) 718-3062</span>|<span>Email: mirelharrowgate@quellmail.example</span>|<span>Address: 58 E. Tamsin Avenue, Ste 410, Corvel Bay, FL 32599</span></div>
  <div class="footer-badges">
    <div class="footer-brand"><span class="mark"></span>Harrowgate</div>
    <div class="badge" style="width:50px;height:36px;border-radius:4px"></div>
    <div class="badge" style="width:30px;height:36px"></div>
    <div class="badge" style="width:120px;height:36px"></div>
    <div class="badge" style="width:62px;height:36px;border-radius:4px"></div>
  </div>
</footer>

</body>
</html>
```